Sell the dream! Property investment proposal document

We are looking for a proposal document which outlines our vision for property development. The purpose of the document is to raise investment from investors - sell the dream!
Brief summary:
Kestrel Dwellings Developments, is an emerging New Zealand property investment company with a focus on providing unique property investment opportunities.
Our expertise and capabilities in architectural modular homes provide us with a remarkable advantage in tackling the development of properties that are typically considered challenging, remote, or uniquely positioned.
Our specialization in this niche sector of property development not only sets us apart from competitors, but also paves the way for lucrative investment opportunities in the New Zealand property market.
Feel free to use any images from www.kestreldwellings.co.nz
Target Market(s)
investors for a unique property development opportunity
Industry/Entity Type
luxury property development in unique locations throughout New Zealand
Colors
Designer to choose only greyscale colors for use in the design.
Look and feel

```html
<!DOCTYPE html>
<html lang="en">
<head>
<meta charset="utf-8">
<title>Kestrel Dwellings – Proposal Spread</title>
<link href="https://fonts.googleapis.com/css2?family=Inter:wght@300;400&display=swap" rel="stylesheet">
<style>
  :root{
    --charcoal:#2d2b2c;
    --paper:#ffffff;
    --gold:#c4a73a;
    --ink:#2f2d2e;
    --soft-ink:#4a4849;
    --light-text:#f1f0ee;
    --rule-light:#cfcdcb;
    --rule-grey:#a9a7a6;
    --muted:#8d8b8a;
  }
  *{margin:0;padding:0;box-sizing:border-box}
  html,body{width:1200px;height:846px;overflow:hidden;background:var(--paper)}
  body{font-family:"Inter",sans-serif;font-weight:300;position:relative}
  .spread{position:relative;width:1200px;height:846px}
  .page-left{position:absolute;left:0;top:0;width:600px;height:846px;background:var(--charcoal)}
  .page-right{position:absolute;left:600px;top:0;width:600px;height:846px;background:var(--paper)}
  .abs{position:absolute}
  .rule{position:absolute;height:2px}
  .rule-about{left:37px;top:46px;width:71px;background:var(--rule-light)}
  .rule-approach{left:633px;top:522px;width:156px;height:3px;background:var(--rule-grey)}
  .section-title{position:absolute;color:var(--gold);font-weight:300;font-size:24px;letter-spacing:-0.2px;line-height:1}
  .about-title{left:46px;top:67px}
  .approach-title{left:646px;top:543px}
  .about-copy{left:46px;top:113px;width:540px;color:var(--light-text);font-size:14.2px;line-height:17.6px;white-space:nowrap;letter-spacing:-0.1px}
  .about-copy p+p{margin-top:10.5px}
  .photo{position:absolute}
  .photo-exterior{left:0;top:242px;width:574px;height:408px;border:1.5px solid var(--gold);
    background:linear-gradient(180deg,#c9cdc4 0%,#6f8061 30%,#1f2220 55%,#2a2d28 75%,#bfc0ba 100%)}
  .photo-bedroom{left:46px;top:572px;width:296px;height:202px;border:2px solid var(--gold);
    background:linear-gradient(90deg,#b3a293 0%,#cdbfb2 45%,#8e8474 80%,#6f7663 100%)}
  .photo-living{left:634px;top:134px;width:566px;height:328px;border:1px solid #3a3837;
    background:linear-gradient(180deg,#8f827b 0%,#c9c7cc 25%,#b9bac2 55%,#a69585 72%,#5d5652 100%)}
  .caption{position:absolute;font-size:10.5px;letter-spacing:0.2px;text-align:right;white-space:nowrap}
  .caption-exterior{right:25px;top:657px;color:var(--light-text)}
  .caption-bedroom{right:258px;top:780px;color:var(--light-text)}
  .caption-living{right:45px;top:469px;color:var(--soft-ink)}
  .brand-name{left:646px;top:60px;font-size:23px;font-weight:300;color:var(--ink);letter-spacing:0.5px}
  .tagline{left:763px;top:49px;font-size:23px;line-height:26px;color:var(--ink);letter-spacing:-0.2px;white-space:nowrap}
  .approach-col{position:absolute;top:590px;font-size:13.9px;line-height:17.4px;color:var(--ink);white-space:nowrap;letter-spacing:-0.1px}
  .approach-col p+p{margin-top:11px}
  .col-one{left:646px}
  .col-two{left:909px}
  .folio{position:absolute;top:806px;font-size:12px;color:var(--muted)}
  .folio-num{color:var(--light-text);border-bottom:1px solid var(--gold);padding-bottom:2px}
  .folio-left-num{left:19px}
  .folio-left-name{left:46px}
  .folio-right-name{right:46px;color:var(--soft-ink)}
  .folio-right-num{right:16px;color:var(--ink)}
</style>
</head>
<body>
<div class="spread">
  <section class="page-left">
    <div class="rule rule-about"></div>
    <h2 class="section-title about-title">About us</h2>
    <div class="abs about-copy">
      <p>Kestrel Dwellings Developments is an emerging New Zealand<br>property investment company with a focus on providing unique<br>property investment opportunities.</p>
      <p>Our specialization in architectural modular homes provide us with a<br>remarkable advantage in tackling the development of properties that are<br>typically considered challenging, remote, or uniquely positioned.</p>
    </div>
    <div class="photo photo-exterior" role="img" aria-label="Dark-clad two-level modular home set among trees with a misty green hill behind"></div>
    <div class="caption caption-exterior">Signature Two Storey No. 1</div>
    <div class="photo photo-bedroom" role="img" aria-label="Bedroom with timber-panelled wall, low bed and tall window to the landscape"></div>
    <div class="caption caption-bedroom">The Studio Collection No. 2</div>
    <span class="folio folio-left-num folio-num">2</span>
    <span class="folio folio-left-name">Kestrel Dwellings</span>
  </section>

  <section class="page-right"></section>
  <div class="abs brand-name">Kestrel</div>
  <div class="abs tagline">Modular, architectural homes<br>with flexibility and sophistication</div>
  <div class="photo photo-living" role="img" aria-label="Living room with large window overlooking calm water, sofa and low timber table"></div>
  <div class="caption caption-living">The Studio Collection No. 2</div>
  <div class="rule rule-approach"></div>
  <h2 class="section-title approach-title">Our unique approach</h2>
  <div class="approach-col col-one">
    <p>Architecturally-designed, highly<br>customisable homes, built off-site,<br>delivered to and assembled on a plot<br>of land anywhere in New Zealand.</p>
    <p>At Kestrel, our aim is to help people<br>envision their own homes; to simplify<br>the process of crafting and building<br>them to exacting standards; and<br>give our customers and their families<br>personalised homes in which to forge<br>memories of shelter and comfort.</p>
  </div>
  <div class="approach-col col-two">
    <p>Our manufacturing processes<br>have been tried, perfected and<br>are independent of weather or site<br>constraints, allowing for an orderly,<br>systematic building phase and rapid<br>turnaround times.</p>
    <p>By delivering prefabricated and<br>ready-to-assemble components to<br>your site, we minimise the number<br>of workers, tools, vehicles and time<br>required on site.</p>
  </div>
  <span class="folio folio-right-name">Sell the dream!</span>
  <span class="folio folio-right-num folio-num">3</span>
</div>
</body>
</html>
```